New Website for Manufacturing Company - PSD only, no coding - CLOSED TO NEW DESIGNERS

IF YOU HAVE NOT ALREADY SUBMITTED A DESIGN PLEASE DO NOT SUBMIT ONE.
This is a re-work of an existing website. We can keep the themes and color schemes the same but we will be changing the layout and page content.
The scope includes the creation of some icons/sketches that will form some of the page content.
The scope is design only, no coding.
There are four files that have been uploaded that give a more detailed project brief, please read them.
Target Market(s)
Manufacturing
Industry/Entity Type
It Company
Number of Pages Required
1 page

```html
<!DOCTYPE html>
<html lang="en">
<head>
<meta charset="utf-8">
<title>Kestrel – High Temperature Insulation</title>
<link href="https://fonts.googleapis.com/css2?family=Open+Sans:wght@400;600;700;800&family=Oswald:wght@400;500&display=swap" rel="stylesheet">
<style>
:root{
  --blue:#1f5fa5;
  --blue-dark:#18508d;
  --blue-light:#e7eef7;
  --ink:#2b2b2b;
  --muted:#6d6d6d;
  --line:#c9d3df;
  --footer:#3b3b3b;
  --footer-deep:#2a2a2a;
  --white:#ffffff;
}
*{box-sizing:border-box;margin:0;padding:0}
html,body{width:672px;height:1200px;overflow:hidden;background:var(--white)}
body{font-family:"Open Sans",Arial,sans-serif;color:var(--ink);position:relative}

/* header */
.site-header{height:74px;display:flex;align-items:center;padding:0 24px;gap:18px}
.brand{display:flex;align-items:center;gap:6px;font-weight:800;font-size:22px;color:var(--blue);letter-spacing:1px;border:2px solid var(--blue);padding:2px 8px}
.brand-dot{width:10px;height:10px;background:var(--blue)}
.tagline{flex:1;text-align:center;font-weight:800;font-size:15px;line-height:18px;letter-spacing:.3px}
.header-contact{text-align:right;font-size:8px;color:var(--muted)}
.header-contact .row{display:flex;gap:10px;justify-content:flex-end;margin-bottom:6px}
.header-contact .row span{display:flex;align-items:center;gap:3px}
.btn-group{display:flex;gap:6px;justify-content:flex-end}
.btn{background:var(--blue);color:var(--white);font-size:8px;font-weight:700;padding:5px 10px;text-transform:uppercase}

/* nav */
.main-nav{height:22px;background:var(--blue);display:flex;justify-content:space-between;padding:0 70px;align-items:center}
.main-nav a{color:var(--white);font-size:8px;font-weight:600;text-decoration:none;text-transform:uppercase}
.main-nav a.active{color:#cfe0f3}

/* hero */
.hero{height:222px;position:relative;background:linear-gradient(180deg,#8f9399 0%,#6c7076 55%,#7d8187 100%);display:flex;flex-direction:column;align-items:center;justify-content:center;gap:18px}
.hero h1{font-family:"Oswald",sans-serif;font-weight:400;color:var(--white);font-size:21px;line-height:25px;text-align:center;letter-spacing:.6px;width:470px;text-transform:uppercase}
.hero .btn{font-size:8px;padding:6px 12px}
.hero-arrow{position:absolute;top:50%;width:10px;height:16px}
.hero-arrow.left{left:14px}.hero-arrow.right{right:14px}

/* welcome */
.welcome{text-align:center;padding-top:20px;height:202px}
.section-title{font-weight:700;font-size:12px;letter-spacing:.5px;text-transform:uppercase}
.welcome .brand{display:inline-flex;margin:10px 0 12px;font-size:20px}
.welcome p{font-size:8px;line-height:13px;color:var(--muted);width:470px;margin:0 auto}

/* divider title */
.divider-title{display:flex;align-items:center;gap:10px;padding:0 56px;height:22px}
.divider-title::before,.divider-title::after{content:"";flex:1;height:1px;background:var(--line)}

/* capabilities */
.capabilities{padding:6px 56px 0;display:grid;grid-template-columns:repeat(4,1fr);gap:12px;height:402px}
.cap-card{border:1px solid var(--line);border-radius:4px;overflow:hidden;display:flex;flex-direction:column;background:var(--white)}
.cap-art{height:112px;margin:8px;border-radius:3px;background:linear-gradient(160deg,#f4f6f8,#dde2e8)}
.cap-card h3{font-size:8px;font-weight:700;text-align:center;text-transform:uppercase;margin-top:4px;color:var(--blue)}
.cap-card p{font-size:7px;line-height:10px;text-align:center;color:var(--muted);padding:4px 10px 0}
.cap-card.featured{background:var(--blue)}
.cap-card.featured h3,.cap-card.featured p{color:var(--white)}

/* services */
.services{display:grid;grid-template-columns:1fr 1fr;gap:40px;padding:12px 70px 0;height:90px}
.service{display:flex;gap:12px;align-items:flex-start}
.service-icon{width:46px;height:46px;border-radius:50%;background:var(--blue);flex:none;display:flex;align-items:center;justify-content:center}
.service h4{font-size:9px;font-weight:700;color:var(--blue);text-transform:uppercase;margin:6px 0 4px}
.service p{font-size:7px;line-height:10px;color:var(--muted)}

/* footer */
.site-footer{position:absolute;left:0;right:0;bottom:0;height:146px;background:var(--footer);color:#cfcfcf}
.footer-cols{display:grid;grid-template-columns:repeat(6,1fr);padding:14px 22px 0;gap:8px;height:106px}
.footer-cols h5{font-size:7px;font-weight:700;color:var(--white);text-transform:uppercase;margin-bottom:6px}
.footer-cols li{list-style:none;font-size:6.5px;line-height:9px}
.footer-bottom{height:40px;background:var(--footer-deep);display:flex;flex-direction:column;align-items:center;justify-content:center;gap:5px;font-size:6.5px}
.social{display:flex;gap:8px}
.social span{width:10px;height:10px;border-radius:50%;background:#d7d7d7}
</style>
</head>
<body>

<header class="site-header">
  <div class="brand"><span class="brand-dot"></span>KESTREL</div>
  <div class="tagline">HIGH TEMPERATURE INSULATION<br>EXPERTS !!!</div>
  <div class="header-contact">
    <div class="row">
      <span><svg width="8" height="8" viewBox="0 0 24 24"><path fill="#1f5fa5" d="M6.6 10.8a15 15 0 0 0 6.6 6.6l2.2-2.2a1 1 0 0 1 1-.25 11 11 0 0 0 3.6.6 1 1 0 0 1 1 1V20a1 1 0 0 1-1 1A17 17 0 0 1 3 4a1 1 0 0 1 1-1h3.5a1 1 0 0 1 1 1 11 11 0 0 0 .6 3.6 1 1 0 0 1-.25 1z"/></svg>555-0142-780</span>
      <span><svg width="8" height="8" viewBox="0 0 24 24"><path fill="#1f5fa5" d="M2 5h20v14H2z M2 5l10 8 10-8" stroke="#fff" stroke-width="1.5"/></svg>info@kestrelthermal.com</span>
    </div>
    <div class="btn-group"><span class="btn">RFQ</span><span class="btn">Call to action</span></div>
  </div>
</header>

<nav class="main-nav">
  <a class="active" href="#">Home</a><a href="#">Capabilities</a><a href="#">Services</a><a href="#">Markets</a><a href="#">Materials</a><a href="#">Documentation</a><a href="#">Contact us</a>
</nav>

<section class="hero" role="img" aria-label="Grey technical sketch of insulation fabrication machinery behind the headline">
  <svg class="hero-arrow left" viewBox="0 0 10 16"><path d="M8 1 2 8l6 7" stroke="#fff" stroke-width="2" fill="none"/></svg>
  <h1>Manufacturer fabricator and distributor of high temperature insulating materials</h1>
  <span class="btn">More about us</span>
  <svg class="hero-arrow right" viewBox="0 0 10 16"><path d="m2 1 6 7-6 7" stroke="#fff" stroke-width="2" fill="none"/></svg>
</section>

<section class="welcome">
  <h2 class="section-title">Welcome to Kestrel</h2>
  <div class="brand"><span class="brand-dot"></span>KESTREL</div>
  <p>We design, cut and supply insulating parts for ovens, furnaces, kilns and appliances. Our team works from your drawing or sample to deliver precise parts in small runs or large volumes. From mica and ceramic fiber to silicone and foam, we hold the stock and the skill to keep your line running at any heat.</p>
</section>

<h2 class="section-title divider-title">Our capabilities</h2>
<section class="capabilities">
  <article class="cap-card featured"><div class="cap-art" role="img" aria-label="Sketch of a waterjet cut part"></div><h3>Waterjet cutting</h3><p>Clean, accurate parts cut to your exact drawing and tolerance.</p></article>
  <article class="cap-card"><div class="cap-art" role="img" aria-label="Sketch of a cast insulating block"></div><h3>Casting</h3><p>Solid shapes cast in refractory mixes for heavy heat duty.</p></article>
  <article class="cap-card"><div class="cap-art" role="img" aria-label="Sketch of a laminated gasket"></div><h3>Laminating</h3><p>Layered sheets bonded together for strength and thermal control.</p></article>
  <article class="cap-card"><div class="cap-art" role="img" aria-label="Sketch of a machined component"></div><h3>CNC machining</h3><p>Complex profiles milled and drilled from rigid insulation boards.</p></article>
  <article class="cap-card"><div class="cap-art" role="img" aria-label="Sketch of slit rolls of tape"></div><h3>Slitting</h3><p>Rolls slit to narrow widths for tapes and wraps quickly.</p></article>
  <article class="cap-card"><div class="cap-art" role="img" aria-label="Sketch of die cut pieces"></div><h3>Die cutting</h3><p>High volume gaskets and washers punched fast and consistently.</p></article>
  <article class="cap-card"><div class="cap-art" role="img" aria-label="Sketch of vacuum formed panels"></div><h3>Vacuum forming</h3><p>Fiber shapes formed into custom curves, tubes and panels.</p></article>
  <article class="cap-card"><div class="cap-art" role="img" aria-label="Sketch of a rolled insulation blanket"></div><h3>Capability</h3><p>Ask our engineers about any other process you may need.</p></article>
</section>

<h2 class="section-title divider-title">Our services</h2>
<section class="services">
  <div class="service">
    <div class="service-icon"><svg width="22" height="22" viewBox="0 0 24 24"><path d="M4 20 20 4M14 4h6v6" stroke="#fff" stroke-width="2" fill="none"/></svg></div>
    <div><h4>Kitting</h4><p>Parts grouped, labelled and packed as ready-to-install kits for your assembly line.</p></div>
  </div>
  <div class="service">
    <div class="service-icon"><svg width="22" height="22" viewBox="0 0 24 24"><path d="M4 20 20 4M4 20l3-8 5 5z" stroke="#fff" stroke-width="2" fill="none"/></svg></div>
    <div><h4>Prototyping</h4><p>Fast sample parts so you can test fit and function before production.</p></div>
  </div>
</section>

<footer class="site-footer">
  <div class="footer-cols">
    <div><h5>Capabilities</h5><ul><li>Waterjet Cutting</li><li>Casting</li><li>Laminating</li><li>CNC Machining</li><li>Slitting</li><li>Die Cutting</li><li>Vacuum Forming</li></ul></div>
    <div><h5>Services</h5><ul><li>Kitting</li><li>Prototyping</li><li>Engineering</li><li>Stocking</li></ul></div>
    <div><h5>Markets</h5><ul><li>Appliances</li><li>Lamps</li><li>Transportation</li><li>Heat Treating</li><li>Aircraft</li></ul></div>
    <div><h5>Materials</h5><ul><li>Mica Sheet</li><li>Ceramic Fiber</li><li>Silicone</li><li>Foam</li><li>Glass Cloth</li><li>Millboard</li></ul></div>
    <div><h5>Documentation</h5><ul><li>ISO &amp; Data Sheets</li><li>Terms &amp; Conditions</li></ul></div>
    <div><h5>Contact</h5><ul><li>RFQ form</li><li>Contact us form</li><li>About us</li></ul></div>
  </div>
  <div class="footer-bottom">
    <div class="social"><span></span><span></span><span></span><span></span></div>
    <div>All Rights Reserved – Copyright Kestrel Thermal</div>
  </div>
</footer>

</body>
</html>
```